Business Card Design

We need the business card for our new business based in St. Marys, we manufacture mainly bubble wraps. And we would like the design to use our company logo and also make it easy for people to understand right away we are bubble wrap manufacturer

Industry/Entity Type

Business

Contact Information for Business Card

Cushtane Pty Ltd, 14 Larkin Road Kelmore NSW 2841, Tel: 02 9471 5826, Fax: 9471 5839, Dara Oyelaran, General Manager, Mobile :0438 217 564, dara.oyelaran@cushtane.com.au, Website: cushtane.com.au

```html
<!DOCTYPE html>
<html lang="en">
<head>
<meta charset="utf-8">
<title>Cushtane Business Card</title>
<link rel="stylesheet" href="https://fonts.googleapis.com/css2?family=Montserrat:wght@400;500;700;800&display=swap">
<style>
  :root {
    --backdrop: #e4e4e4;
    --card: #0d0d0d;
    --card-sheen: #1c1c1c;
    --brand-grey: #7b7b7b;
    --text-grey: #9a9a9a;
    --accent-red: #d0382f;
  }
  * { box-sizing: border-box; margin: 0; padding: 0; }
  html, body {
    width: 1200px; height: 852px; overflow: hidden;
    background: var(--backdrop);
    font-family: "Montserrat", sans-serif;
  }
  .sheet {
    width: 1200px; height: 852px;
    display: flex; align-items: center; justify-content: center; gap: 40px;
  }
  .card {
    width: 540px; height: 330px;
    border-radius: 14px;
    background: linear-gradient(120deg, var(--card) 0%, var(--card-sheen) 45%, var(--card) 70%);
    position: relative;
    box-shadow: 0 6px 18px rgba(0,0,0,0.25);
    overflow: hidden;
  }
  /* Front */
  .card-front {
    display: flex; flex-direction: column; align-items: center; justify-content: center;
  }
  .wordmark {
    color: var(--brand-grey);
    font-weight: 800;
    font-size: 62px;
    letter-spacing: 1px;
    line-height: 1;
  }
  .tagline {
    margin-top: 14px;
    color: var(--brand-grey);
    font-weight: 500;
    font-size: 13.5px;
    letter-spacing: 6.4px;
    text-transform: uppercase;
  }
  /* Back */
  .card-back { padding: 0 30px; display: flex; align-items: center; gap: 28px; }
  .back-brand {
    width: 170px; flex: none;
    display: flex; align-items: center; gap: 8px;
  }
  .back-brand-square {
    width: 14px; height: 14px; flex: none;
    background: var(--accent-red);
  }
  .back-brand-name {
    color: var(--accent-red);
    font-weight: 800;
    font-size: 24px;
    letter-spacing: 0.5px;
    line-height: 1;
  }
  .contact { color: var(--text-grey); font-size: 13px; line-height: 1.55; }
  .contact-name {
    color: var(--accent-red); font-weight: 700; font-size: 17px;
    text-transform: uppercase; letter-spacing: 0.5px; line-height: 1.2;
  }
  .contact-title { font-size: 11.5px; margin-bottom: 12px; }
  .contact-address { margin-bottom: 2px; }
  .contact-list { list-style: none; }
  .contact-list li { display: flex; align-items: center; gap: 9px; }
  .contact-list svg { width: 12px; height: 12px; fill: var(--accent-red); flex: none; }
</style>
</head>
<body>
<main class="sheet">
  <section class="card card-front">
    <div class="wordmark">CUSHTANE</div>
    <div class="tagline">Protective Packaging Solutions</div>
  </section>

  <section class="card card-back">
    <div class="back-brand">
      <span class="back-brand-square"></span>
      <span class="back-brand-name">CUSHTANE</span>
    </div>
    <div class="contact">
      <div class="contact-name">Dara Oyelaran</div>
      <div class="contact-title">General Manager</div>
      <div class="contact-address">14 Larkin Road Kelmore NSW 2841</div>
      <ul class="contact-list">
        <li><svg viewBox="0 0 12 12"><path d="M1 4c0-2 2-3 5-3s5 1 5 3v1H8V4H4v1H1zM2 6h8l1 5H1z"/></svg>02 9471 5826</li>
        <li><svg viewBox="0 0 12 12"><rect x="3" y="1" width="6" height="3"/><rect x="1" y="4" width="10" height="5" rx="1"/><rect x="3" y="8" width="6" height="3"/></svg>9471 5839</li>
        <li><svg viewBox="0 0 12 12"><path d="M3 0h6a1 1 0 0 1 1 1v10a1 1 0 0 1-1 1H3a1 1 0 0 1-1-1V1a1 1 0 0 1 1-1zm0 2v7h6V2z"/></svg>0438 217 564</li>
        <li><svg viewBox="0 0 12 12"><path d="M0 2h12v1L6 7 0 3zM0 4.5l6 4 6-4V10H0z"/></svg>dara.oyelaran@cushtane.com.au</li>
        <li><svg viewBox="0 0 12 12"><circle cx="6" cy="6" r="5.5"/></svg>www.cushtane.com.au</li>
      </ul>
    </div>
  </section>
</main>
</body>
</html>
```